Structural Engineering Business Card

Brookvane Drafting does residential house plans for clients in Central Florida. Would like simple but elegant business card that is appropriate for a house plan engineering company. Prefer black business card with black/white them but open to other shades of blue. I uploaded a sample card that I came across that looked good but please come up with your own creative designs.

Contact Information for Business Card

Name, Title, Phone, Email, Address, website

```html
<!DOCTYPE html>
<html lang="en">
<head>
<meta charset="UTF-8">
<title>Brookvane Drafting Business Card</title>
<link href="https://fonts.googleapis.com/css2?family=Montserrat:wght@400;500;800&display=swap" rel="stylesheet">
<style>
  :root {
    --bg: #c9c9c9;
    --card-black: #050505;
    --card-white: #ffffff;
    --swoosh-grey: #6b6b6b;
    --name-grey: #7a7a7a;
    --icon-grey: #8a8a8a;
  }
  html, body {
    margin: 0;
    padding: 0;
    width: 1200px;
    height: 1200px;
    overflow: hidden;
    background: var(--bg);
    font-family: "Montserrat", sans-serif;
  }
  .canvas {
    position: relative;
    width: 1200px;
    height: 1200px;
  }
  .card {
    position: absolute;
    left: 250px;
    width: 700px;
    height: 400px;
    background: var(--card-black);
    overflow: hidden;
    box-shadow: 0 14px 30px rgba(0,0,0,0.25);
  }
  .card-front { top: 150px; }
  .card-back { top: 650px; }
  .card-art {
    position: absolute;
    inset: 0;
  }
  .brand-name {
    position: absolute;
    margin: 0;
    font-weight: 800;
    letter-spacing: 0.5px;
    text-transform: uppercase;
    white-space: nowrap;
  }
  .card-front .brand-name {
    color: var(--card-black);
    font-size: 30px;
    line-height: 1.1;
    left: 440px;
    width: 230px;
    top: 95px;
    text-align: center;
  }
  .card-back .brand-name {
    color: var(--card-white);
    font-size: 46px;
    left: 0;
    right: 0;
    top: 170px;
    text-align: center;
  }
  .contact {
    position: absolute;
    left: 52px;
    top: 150px;
    color: var(--card-white);
    font-size: 16px;
    line-height: 1.35;
  }
  .address { margin: 0 0 14px 0; }
  .contact-list {
    list-style: none;
    margin: 0;
    padding: 0;
  }
  .contact-list li {
    display: flex;
    align-items: center;
    gap: 10px;
  }
  .contact-list svg {
    width: 13px;
    height: 13px;
    fill: var(--icon-grey);
  }
  .person {
    position: absolute;
    right: 60px;
    bottom: 26px;
    text-align: right;
  }
  .person-name {
    margin: 0;
    color: var(--name-grey);
    font-weight: 800;
    font-size: 22px;
    letter-spacing: 1px;
  }
  .person-title {
    margin: 2px 0 0 0;
    color: var(--card-white);
    font-size: 15px;
    font-weight: 500;
  }
</style>
</head>
<body>
<div class="canvas">

  <section class="card card-front">
    <svg class="card-art" viewBox="0 0 700 400" width="700" height="400" aria-hidden="true">
      <path d="M300 0 C370 150 470 270 700 308 L700 300 C485 268 392 140 336 0 Z" fill="var(--swoosh-grey)"/>
      <path d="M336 0 C392 140 485 268 700 300 L700 0 Z" fill="var(--card-white)"/>
      <path d="M290 0 C362 155 462 278 700 316" fill="none" stroke="var(--card-white)" stroke-width="2"/>
    </svg>
    <p class="brand-name">Brookvane<br>Drafting</p>

    <div class="contact">
      <p class="address">218 Cedar Run Lane<br>Ocala, FL 34470</p>
      <ul class="contact-list">
        <li><svg viewBox="0 0 24 24"><path d="M6.6 10.8a15.1 15.1 0 0 0 6.6 6.6l2.2-2.2a1 1 0 0 1 1-.25 11.4 11.4 0 0 0 3.6.57 1 1 0 0 1 1 1V20a1 1 0 0 1-1 1A17 17 0 0 1 3 4a1 1 0 0 1 1-1h3.5a1 1 0 0 1 1 1c0 1.25.2 2.45.57 3.57a1 1 0 0 1-.25 1z"/></svg>(555) 304-7718</li>
        <li><svg viewBox="0 0 24 24"><path d="M2 5h20v14H2z M2 5l10 8 10-8" /></svg>hello@brookvane.com</li>
        <li><svg viewBox="0 0 24 24"><circle cx="12" cy="12" r="10"/></svg>www.brookvanedrafting.com</li>
      </ul>
    </div>

    <div class="person">
      <p class="person-name">DALTON REESE</p>
      <p class="person-title">Owner</p>
    </div>
  </section>

  <section class="card card-back">
    <p class="brand-name">Brookvane Drafting</p>
  </section>

</div>
</body>
</html>
```